Business card for medical clinic

I need an upmarket, modern medical/health business card for my clinic

Contact Information for Business Card

name, address, email, qr code

```html
<!DOCTYPE html>
<html lang="en">
<head>
<meta charset="UTF-8">
<title>Aster Vale Clinic – Business Card</title>
<link href="https://fonts.googleapis.com/css2?family=Poppins:wght@300;400;500;700&display=swap" rel="stylesheet">
<style>
  :root {
    --backdrop: #222222;
    --card: #1c1c1c;
    --blue: #1e9fdc;
    --white: #f4f6f8;
  }
  * { margin: 0; padding: 0; box-sizing: border-box; }
  html, body {
    width: 1200px; height: 711px; overflow: hidden;
    background: var(--backdrop);
    font-family: "Poppins", sans-serif;
  }
  .stage {
    position: relative; width: 1200px; height: 711px;
    display: flex; align-items: center; justify-content: center; gap: 40px;
  }
  .card {
    position: relative; width: 540px; height: 309px;
    background: var(--card);
    border-bottom: 4px solid var(--blue);
  }
  .brand {
    display: flex; align-items: center; gap: 14px;
    color: var(--blue); font-weight: 500; letter-spacing: 0.06em;
    text-transform: uppercase; white-space: nowrap;
  }
  .brand-dot {
    border: 3px solid var(--blue); border-radius: 50%; flex: none;
  }
  .card-front .brand {
    position: absolute; left: 50%; top: 50%; transform: translate(-50%, -50%);
    font-size: 30px;
  }
  .card-front .brand-dot { width: 56px; height: 56px; }
  .card-back .brand {
    position: absolute; left: 38px; top: 50%; transform: translateY(-50%);
    font-size: 16px; gap: 9px;
  }
  .card-back .brand-dot { width: 32px; height: 32px; border-width: 2px; }
  .divider {
    position: absolute; left: 262px; top: 62px; width: 1px; height: 190px;
    background: var(--blue);
  }
  .details { position: absolute; left: 290px; top: 54px; }
  .person-name { font-size: 29px; color: var(--blue); line-height: 1.1; }
  .person-name .first { font-weight: 700; }
  .person-name .last { font-weight: 300; }
  .person-title { color: var(--white); font-size: 12.5px; font-weight: 500; margin-top: 4px; }
  .address { color: var(--blue); font-size: 12.5px; line-height: 1.45; margin-top: 14px; }
  .contacts { list-style: none; margin-top: 16px; }
  .contacts li {
    display: flex; align-items: center; gap: 9px;
    color: var(--white); font-size: 12.5px; line-height: 1; margin-bottom: 10px;
  }
  .contacts svg { width: 14px; height: 14px; flex: none; }
</style>
</head>
<body>
<main class="stage">
  <section class="card card-front">
    <div class="brand"><span class="brand-dot"></span>Aster Vale Clinic</div>
  </section>

  <section class="card card-back">
    <div class="brand"><span class="brand-dot"></span>Aster Vale Clinic</div>
    <div class="divider"></div>
    <div class="details">
      <h1 class="person-name"><span class="first">Lena</span> <span class="last">Marovic</span></h1>
      <p class="person-title">Founder &amp; CEO</p>
      <p class="address">1840 Brookline Ave. Suite 310<br>Dayton, OH 45402</p>
      <ul class="contacts">
        <li>
          <svg viewBox="0 0 24 24" fill="var(--blue)" aria-hidden="true"><path d="M6.6 10.8a15.1 15.1 0 0 0 6.6 6.6l2.2-2.2a1 1 0 0 1 1-.25 11.4 11.4 0 0 0 3.6.57 1 1 0 0 1 1 1V20a1 1 0 0 1-1 1A17 17 0 0 1 3 4a1 1 0 0 1 1-1h3.5a1 1 0 0 1 1 1c0 1.25.2 2.45.57 3.57a1 1 0 0 1-.25 1z"/></svg>
          (937) 555-0148
        </li>
        <li>
          <svg viewBox="0 0 24 24" fill="none" stroke="var(--blue)" stroke-width="2" aria-hidden="true"><rect x="3" y="5" width="18" height="14" rx="1"/><path d="M3 6l9 7 9-7"/></svg>
          info@astervaleclinic.com
        </li>
        <li>
          <svg viewBox="0 0 24 24" fill="none" stroke="var(--blue)" stroke-width="2" aria-hidden="true"><circle cx="12" cy="12" r="9"/><path d="M3 12h18M12 3c3 3.2 3 14.8 0 18M12 3c-3 3.2-3 14.8 0 18"/></svg>
          www.astervaleclinic.com
        </li>
      </ul>
    </div>
  </section>
</main>
</body>
</html>
```